Business card design for international hub site

I need a business card design with the logo attached. Although the site is for the teenage audience (it is about the high school graduation ball, the Prom), the business card is for professional use to be given to professional contacts (B2B), such as suppliers and partners, so it needs to look professional (but also girly, glamours and clean).

Target Market(s)

B2B

Industry/Entity Type

Media

Colors
eea4c8
f9d9e8
e667a6
9d9d9d
1b1b1b

Requirements
Must have
• Space for Name, Tile, Address, Phone, email and website.
Should not have
• Photo

```html
<!DOCTYPE html>
<html lang="en">
<head>
<meta charset="UTF-8">
<title>Promvine Business Card</title>
<link href="https://fonts.googleapis.com/css2?family=Pinyon+Script&family=Roboto:wght@400;700&display=swap" rel="stylesheet">
<style>
  :root {
    --pink-light: #f9d9e8;
    --pink-soft: #eea4c8;
    --pink-strong: #e667a6;
    --grey: #9d9d9d;
    --ink: #1b1b1b;
    --stage: #2b2b2b;
    --card-white: #fbf3f6;
  }
  * { box-sizing: border-box; margin: 0; padding: 0; }
  html, body { width: 1200px; height: 997px; overflow: hidden; }
  body {
    background: var(--stage);
    font-family: "Roboto", Arial, sans-serif;
    position: relative;
  }
  .card {
    position: absolute;
    left: 250px;
    width: 700px;
    height: 400px;
    border-radius: 18px;
    overflow: hidden;
    background: var(--card-white);
  }
  .card--front { top: 70px; }
  .card--back { top: 527px; }

  .bokeh-field { position: absolute; inset: 0; }
  .card--front .bokeh-field {
    background:
      radial-gradient(ellipse 60% 45% at 65% 60%, rgba(230,103,166,.75), rgba(238,164,200,.35) 60%, transparent 80%),
      radial-gradient(ellipse 40% 30% at 20% 85%, rgba(230,103,166,.55), transparent 75%),
      linear-gradient(160deg, var(--card-white) 0%, var(--pink-light) 45%, var(--pink-soft) 100%);
  }
  .card--back .bokeh-field {
    background:
      radial-gradient(ellipse 70% 35% at 55% 20%, rgba(230,103,166,.85), rgba(238,164,200,.4) 60%, transparent 85%),
      linear-gradient(180deg, var(--pink-soft) 0%, var(--pink-light) 45%, var(--card-white) 100%);
  }

  .brand {
    position: absolute;
    display: flex;
    align-items: center;
    gap: 8px;
    font-family: "Roboto", Arial, sans-serif;
    font-weight: 400;
    font-size: 30px;
    color: var(--grey);
    letter-spacing: .5px;
  }
  .brand__dot {
    width: 12px; height: 12px;
    border-radius: 50%;
    background: var(--pink-strong);
  }
  .card--front .brand { top: 34px; right: 40px; }
  .card--back .brand { top: 250px; right: 40px; }

  .website {
    position: absolute;
    top: 120px; right: 40px;
    font-size: 16px;
    font-weight: 700;
    color: var(--pink-strong);
  }
  .person { position: absolute; left: 40px; top: 150px; }
  .person__name {
    font-size: 20px;
    font-weight: 700;
    color: var(--pink-strong);
    text-transform: uppercase;
  }
  .person__title { font-size: 14px; color: var(--ink); margin-top: 3px; }

  .contacts {
    position: absolute;
    left: 40px; bottom: 34px;
    list-style: none;
    font-size: 15px;
    color: var(--ink);
    line-height: 1.35;
  }
  .contacts li { display: flex; align-items: flex-start; gap: 10px; margin-top: 4px; }
  .contacts .icon {
    flex: none;
    width: 18px; height: 18px;
    margin-top: 1px;
  }

  .tagline {
    position: absolute;
    left: 0; right: 0; top: 150px;
    text-align: center;
    font-family: "Pinyon Script", cursive;
    font-size: 38px;
    color: var(--ink);
    line-height: 1.25;
  }
  .tagline__amp { display: block; font-size: 34px; }
</style>
</head>
<body>
  <section class="card card--front">
    <div class="bokeh-field" role="img" aria-label="Soft pink bokeh light background"></div>
    <div class="brand"><span class="brand__dot"></span>promvine</div>
    <p class="website">www.galaverse.com</p>
    <div class="person">
      <p class="person__name">Clara Benton</p>
      <p class="person__title">Marketing Director</p>
    </div>
    <ul class="contacts">
      <li>
        <svg class="icon" viewBox="0 0 18 18"><circle cx="9" cy="9" r="9" fill="var(--pink-strong)"/><path d="M6 5h2l1 2.5-1.2 1a5 5 0 0 0 2.7 2.7l1-1.2L14 11v2a1 1 0 0 1-1 1A9 9 0 0 1 5 6a1 1 0 0 1 1-1z" fill="#fff"/></svg>
        (800) 555-0142
      </li>
      <li>
        <svg class="icon" viewBox="0 0 18 18"><circle cx="9" cy="9" r="9" fill="var(--pink-strong)"/><rect x="5" y="6" width="8" height="6" rx="1" fill="none" stroke="#fff" stroke-width="1.3"/><path d="M7 13v1.5h4V13" fill="none" stroke="#fff" stroke-width="1.3"/></svg>
        (555) 304-7719
      </li>
      <li>
        <svg class="icon" viewBox="0 0 18 18"><circle cx="9" cy="9" r="9" fill="var(--pink-strong)"/><rect x="4.5" y="6" width="9" height="6.5" rx="1" fill="none" stroke="#fff" stroke-width="1.2"/><path d="M4.8 6.3 9 9.6l4.2-3.3" fill="none" stroke="#fff" stroke-width="1.2"/></svg>
        cbenton@galaverse.com
      </li>
      <li>
        <svg class="icon" viewBox="0 0 18 18"><circle cx="9" cy="9" r="9" fill="var(--pink-strong)"/><path d="M9 14s-3.5-3.6-3.5-6a3.5 3.5 0 0 1 7 0c0 2.4-3.5 6-3.5 6z" fill="#fff"/><circle cx="9" cy="8" r="1.2" fill="var(--pink-strong)"/></svg>
        <span>48 Maple Court Drive, 2nd Floor<br>Riverton, GA 30100</span>
      </li>
    </ul>
  </section>

  <section class="card card--back">
    <div class="bokeh-field" role="img" aria-label="Soft pink bokeh light background"></div>
    <p class="tagline">About the high school graduation ball<span class="tagline__amp">&amp;</span>the Prom</p>
    <div class="brand"><span class="brand__dot"></span>promvine</div>
  </section>
</body>
</html>
```